Business Cards for a law firm

Business cards for our law firm. Use our silhoette logo and OAK PARTNERS - check our website (www.oakpartners.example)

Contact Information for Business Card

our silhouette logo, OAK PARTNERS, 800-555-0147, Dorian Pemberton, dorian@oakpartners.example

Requirements
Must have
• our silhouette logo, OAK PARTNERS, 800-555-0147, Dorian Pemberton, dorian@oakpartners.example

```html
<!DOCTYPE html>
<html lang="en">
<head>
<meta charset="utf-8">
<title>Oak Partners – Business Cards</title>
<link rel="stylesheet" href="https://fonts.googleapis.com/css2?family=Cinzel:wght@600&family=Arimo:wght@400&display=swap">
<style>
  :root {
    --stage: #3a3a3a;
    --navy: #1b2f6b;
    --navy-pattern: #1f3a8a;
    --pattern-light: #3d63c9;
    --paper: #ffffff;
    --ink-light: #ffffff;
  }
  html, body {
    margin: 0;
    padding: 0;
    width: 1200px;
    height: 689px;
    overflow: hidden;
    background: var(--stage);
  }
  .canvas {
    position: relative;
    width: 1200px;
    height: 689px;
    display: flex;
    align-items: center;
    justify-content: center;
    gap: 40px;
  }
  .card {
    position: relative;
    width: 560px;
    height: 320px;
    border-radius: 18px;
    overflow: hidden;
  }
  /* Back of card */
  .card-back {
    background: var(--navy-pattern);
  }
  .card-back .pattern-area {
    position: absolute;
    inset: 0;
    background: linear-gradient(110deg, var(--navy-pattern) 0%, #2346a3 60%, var(--pattern-light) 100%);
  }
  /* Front of card */
  .card-front {
    background: var(--paper);
  }
  .card-front .shape {
    position: absolute;
    inset: 0;
  }
  .brand {
    position: absolute;
    left: 36px;
    top: 122px;
    display: flex;
    align-items: center;
    gap: 11px;
  }
  .brand-dot {
    width: 28px;
    height: 28px;
    border-radius: 50%;
    background: var(--navy);
  }
  .brand-name {
    font-family: "Cinzel", serif;
    font-weight: 600;
    font-size: 22px;
    letter-spacing: 1.5px;
    color: var(--navy);
    white-space: nowrap;
  }
  .contact {
    position: absolute;
    right: 22px;
    top: 72px;
    list-style: none;
    margin: 0;
    padding: 0;
    font-family: "Arimo", Arial, sans-serif;
    font-size: 11px;
    line-height: 16px;
    color: var(--ink-light);
    text-align: right;
  }
  .contact li {
    display: flex;
    align-items: center;
    justify-content: flex-end;
    gap: 6px;
    white-space: nowrap;
  }
  .contact svg {
    width: 10px;
    height: 10px;
    fill: var(--ink-light);
  }
  .person-name {
    position: absolute;
    right: 22px;
    top: 196px;
    margin: 0;
    font-family: "Cinzel", serif;
    font-weight: 600;
    font-size: 16px;
    letter-spacing: 0.5px;
    color: var(--ink-light);
    white-space: nowrap;
  }
</style>
</head>
<body>
<main class="canvas">
  <section class="card card-back" aria-label="Card back">
    <div class="pattern-area" role="img" aria-label="Repeating pattern of the silhouette logo in shades of blue"></div>
  </section>

  <section class="card card-front" aria-label="Card front">
    <svg class="shape" viewBox="0 0 560 320" aria-hidden="true">
      <path d="M300 0 C 335 60, 345 200, 320 320 L560 320 L560 0 Z" fill="var(--navy)"/>
      <path d="M286 0 C 321 60, 331 200, 306 320" fill="none" stroke="var(--navy)" stroke-width="5"/>
    </svg>

    <div class="brand">
      <span class="brand-dot"></span>
      <span class="brand-name">OAK PARTNERS</span>
    </div>

    <ul class="contact">
      <li>800-555-0147
        <svg viewBox="0 0 24 24"><path d="M6.6 10.8a15 15 0 0 0 6.6 6.6l2.2-2.2a1 1 0 0 1 1-.25 11.4 11.4 0 0 0 3.6.57 1 1 0 0 1 1 1V20a1 1 0 0 1-1 1A17 17 0 0 1 3 4a1 1 0 0 1 1-1h3.5a1 1 0 0 1 1 1c0 1.25.2 2.45.57 3.6a1 1 0 0 1-.25 1z"/></svg>
      </li>
      <li>dorian@oakpartners.example
        <svg viewBox="0 0 24 24"><path d="M2 5h20v14H2z M2 5l10 8 10-8" fill="none" stroke="#fff" stroke-width="2"/></svg>
      </li>
      <li>www.oakpartners.example
        <svg viewBox="0 0 24 24"><circle cx="12" cy="12" r="10"/></svg>
      </li>
    </ul>

    <h1 class="person-name">Dorian Pemberton</h1>
  </section>
</main>
</body>
</html>
```